sydney wedding photography business needs a business card design

we need a business card design for a sydney based wedding photography and videography business. our business name is :golden hour studio and film. our target clients are 24-35 yrs female. our style is candid, organic, natural, dynamic. we are a team of young photographers and videographers, and help brides to create memories that they will cherish for the rest of their lives. the logo will be provided. we want an elegant design that reflects our style, and also want to give a great impression to our clients that we are one of the best studios in sydney and our brand means quality and premium service.

Target Market(s)

bride to be, 24-35 years old, living in sydney and surrunding areas

Industry/Entity Type

Wedding Photography

Contact Information for Business Card

address: 57 tarrant street, glenmore nsw 2047
mobile: 0431872259
phone: (02) 9163 2408
info@tidewillowstudio.net.au
www.tidewillowstudio.net.au
facebook:tidewillowweddings
instagram:tidewillowweddings

Font styles to use
Serif
Sans Serif

Requirements
Nice to have
• maybe add my slogan"memories beyond eternity" if the layout looks good
Should not have
• no black color, not good idea for wedding biz card

```html
<!DOCTYPE html>
<html lang="en">
<head>
<meta charset="utf-8">
<title>Golden Hour Studio and Film – Business Card</title>
<link rel="stylesheet" href="https://fonts.googleapis.com/css2?family=Hind:wght@400;500;600&display=swap">
<style>
  :root {
    --page-bg: #ece8e2;
    --gold-light: #f4cb55;
    --gold-mid: #e3a423;
    --gold-deep: #bf7a16;
    --ink: #3b2610;
    --ink-soft: #4a3018;
    --panel-bronze: #5a3a1d;
    --facet-light: #7a5126;
    --facet-deep: #4a2f16;
    --brand-gold: #f2c75c;
  }
  html, body {
    margin: 0;
    padding: 0;
    width: 1200px;
    height: 969px;
    overflow: hidden;
    background: var(--page-bg);
  }
  .business-card {
    position: absolute;
    left: 100px;
    top: 200px;
    width: 1000px;
    height: 566px;
    overflow: hidden;
    background: linear-gradient(160deg, var(--gold-light) 0%, var(--gold-mid) 45%, var(--gold-deep) 100%);
    box-shadow: 0 10px 30px rgba(60,40,20,0.18);
    font-family: "Hind", Arial, sans-serif;
    color: var(--ink);
  }
  .accent-panel {
    position: absolute;
    inset: 0;
    width: 1000px;
    height: 566px;
  }
  .contact-block {
    position: absolute;
    left: 46px;
    top: 0;
  }
  .holder-name {
    position: absolute;
    top: 40px;
    margin: 0;
    font-size: 33px;
    font-weight: 500;
    letter-spacing: 0.5px;
    white-space: nowrap;
  }
  .holder-role {
    position: absolute;
    top: 84px;
    margin: 0;
    font-size: 23px;
    font-weight: 400;
    white-space: nowrap;
  }
  .address {
    position: absolute;
    top: 232px;
    margin: 0;
    font-size: 24px;
    line-height: 36px;
    font-style: normal;
    text-transform: uppercase;
    white-space: nowrap;
  }
  .contact-lines {
    position: absolute;
    top: 322px;
    margin: 0;
    padding: 0;
    list-style: none;
    font-size: 24px;
    line-height: 38px;
    white-space: nowrap;
    text-transform: uppercase;
  }
  .contact-lines .label { font-weight: 600; }
  .social-line {
    position: absolute;
    top: 500px;
    display: flex;
    align-items: center;
    gap: 10px;
    font-size: 22px;
    text-transform: uppercase;
    white-space: nowrap;
    color: var(--ink-soft);
  }
  .social-dot {
    width: 24px;
    height: 24px;
    border-radius: 50%;
    background: var(--ink);
  }
  .brand-name {
    position: absolute;
    left: 505px;
    top: 106px;
    width: 446px;
    margin: 0;
    text-align: center;
    font-size: 33px;
    font-weight: 500;
    letter-spacing: 0.5px;
    color: var(--brand-gold);
    white-space: nowrap;
  }
</style>
</head>
<body>
  <div class="business-card">
    <svg class="accent-panel" viewBox="0 0 1000 566" xmlns="http://www.w3.org/2000/svg">
      <defs>
        <linearGradient id="gemTone" x1="0" y1="0" x2="1" y2="1">
          <stop offset="0" stop-color="var(--facet-light)"/>
          <stop offset="1" stop-color="var(--facet-deep)"/>
        </linearGradient>
      </defs>
      <polygon points="400,0 1000,0 1000,566 572,566" fill="var(--panel-bronze)"/>
      <polygon role="img" aria-label="Large faceted gem decoration" points="412,48 600,0 1000,0 1000,300 650,480" fill="url(#gemTone)" opacity="0.8"/>
    </svg>

    <div class="contact-block">
      <h1 class="holder-name">LIAM HARTLEY</h1>
      <p class="holder-role">CEO/FOUNDER</p>
      <address class="address">57 Tarrant Street<br>Glenmore NSW 2047</address>
      <ul class="contact-lines">
        <li><span class="label">Phone :</span> (02) 9163 2408</li>
        <li><span class="label">Cell :</span> (04) 3187 2259</li>
        <li>info@tidewillowstudio.net.au</li>
        <li>www.tidewillowstudio.net.au</li>
      </ul>
      <div class="social-line"><span class="social-dot"></span>tidewillowweddings</div>
    </div>

    <p class="brand-name">Golden Hour Studio and Film</p>
  </div>
</body>
</html>
```